New Interrior Decoration company needs new website

We need a website for our new company specialising in interior decoration to residential and commercial markets.
We supply and install decorative and printed films for office and home decoration such as feature walls.
We would like to keep the design simple and clean.

Target Market(s)

Architects and interior designaers

Industry/Entity Type

It Company

Number of Pages Required

5+ page

Font styles to use
Sans Serif

Requirements
Must have
• Home page,
• Services/products page (split into commercial and residential)
• Gallery (split into commercial and residential)
• contact form and page
Nice to have
• Very clean and minimalistic design.

```html
<!DOCTYPE html>
<html lang="en">
<head>
<meta charset="utf-8">
<title>Lumen Interiors</title>
<link href="https://fonts.googleapis.com/css2?family=Roboto:wght@400;500;700&display=swap" rel="stylesheet">
<style>
:root{
  --ink:#0c0c0c;
  --blue:#0b5ec6;
  --blue-btn:#1466d2;
  --white:#ffffff;
  --muted:#9a9a9a;
  --footer:#1b1c1e;
  --band:#eeeeee;
  --text-dark:#222;
}
*{box-sizing:border-box;margin:0;padding:0}
html,body{width:1200px;height:3967px;overflow:hidden}
body{font-family:"Roboto",Helvetica,Arial,sans-serif;background:var(--white);color:var(--white)}
.hero{position:relative;height:630px;overflow:hidden}
.hero-photo{position:absolute;inset:0;background:linear-gradient(180deg,#5e6266 0%,#8b8f92 35%,#4a4d50 70%,#232427 100%)}
.hero-shade{position:absolute;inset:0;background:linear-gradient(180deg,rgba(0,0,0,.25),rgba(0,0,0,.35) 60%,rgba(0,0,0,.75))}
.nav{position:absolute;top:46px;left:96px;display:flex;gap:34px;font-size:17px;font-weight:500}
.brand{position:absolute;top:140px;left:0;right:0;display:flex;justify-content:center;align-items:center;gap:12px}
.brand-mark{width:46px;height:46px;background:var(--blue)}
.brand-name{font-size:30px;font-weight:700;letter-spacing:1px;text-transform:uppercase;color:var(--white)}
.hero-title{position:absolute;top:282px;width:100%;text-align:center;font-size:36px;font-weight:700}
.hero-sub{position:absolute;top:340px;width:100%;text-align:center;font-size:17px;font-weight:500;letter-spacing:1px;text-transform:uppercase}
.signup{position:absolute;top:548px;left:0;right:0;display:flex;justify-content:center}
.signup-field{width:282px;height:40px;background:var(--white);color:#777;font-size:13px;padding:12px 14px}
.signup-btn{width:120px;height:40px;background:var(--blue-btn);font-size:15px;font-weight:500;display:flex;align-items:center;justify-content:center}
.service{display:grid;margin-top:4px}
.service.dark{grid-template-columns:640px 560px}
.service.light{grid-template-columns:545px 655px}
.panel{display:flex;flex-direction:column;justify-content:center;padding:0 48px;text-align:center}
.panel.dark{background:var(--ink)}
.panel.blue{background:var(--blue)}
.panel h2{font-size:25px;font-weight:700;margin-bottom:16px}
.panel p{font-size:14px;line-height:1.45}
.photo{height:100%}
.cta{height:82px;background:var(--band);display:flex;align-items:center;justify-content:center;gap:44px}
.cta-text{font-size:27px;color:var(--text-dark)}
.cta-btn{background:var(--blue-btn);color:var(--white);font-size:16px;font-weight:500;padding:12px 24px}
.footer{position:relative;height:447px;background:var(--footer);color:var(--muted)}
.footer .brand{top:42px;left:140px;right:auto;justify-content:flex-start;gap:10px}
.footer .brand-mark{width:32px;height:32px}
.footer .brand-name{font-size:21px}
.footer-about{position:absolute;top:108px;left:140px;width:500px;font-size:13px;line-height:1.5}
.footer-copy{position:absolute;top:196px;left:140px;font-size:12px}
.col{position:absolute;top:46px;font-size:13px;line-height:1.7}
.col h3{color:var(--white);font-size:15px;font-weight:500;margin-bottom:8px}
.col.contact{left:695px}
.col.follow{left:925px}
.socials{display:flex;gap:10px}
.socials span{width:26px;height:26px;border-radius:50%;background:#3b3c3f}
.payments{position:absolute;top:288px;left:140px;display:flex;gap:16px}
.payments span{width:52px;height:26px;border-radius:3px;background:#3a3b3e}
.to-top{position:absolute;top:290px;left:990px;display:flex;align-items:center;gap:14px;color:var(--white);font-size:14px}
</style>
</head>
<body>
<header class="hero">
  <div class="hero-photo" role="img" aria-label="Photograph of a bright modern interior with decorated walls"></div>
  <div class="hero-shade"></div>
  <nav class="nav"><span>About</span><span>Services</span><span>Gallery</span><span>Contact</span></nav>
  <div class="brand"><span class="brand-mark"></span><span class="brand-name">Lumen Interiors</span></div>
  <h1 class="hero-title">Stylish, Innovative Workmanship</h1>
  <p class="hero-sub">Symbol of extraordinary space and great design</p>
  <div class="signup"><div class="signup-field">Enter your email here</div><div class="signup-btn">Quote Today</div></div>
</header>

<section class="service dark" style="height:308px">
  <div class="panel dark"><h2>Interior Decoration</h2><p>Lumen Interiors are involved in all aspects of the interior decoration process, from conception to completion. We work with interior designers and architects to achieve specific project requirements and we are also involved in the ideas and initialisation stages to help create the right interior environment for every need. The variety of looks and finishes that we offer, mixed with the varied trend and design skills we have, means that we are the right fit for all high quality interior projects. We offer specialty services in Kitchen Rejuvenation and Refurbishing, Custom Feature Walls and Decorative Films and Coverings for Interior Walls and Windows. Whatever the need, Lumen Interiors has a solution for you.</p></div>
  <div class="photo" role="img" aria-label="Photograph of a lounge with a sculptural chair" style="background:linear-gradient(135deg,#cfc9d6,#7d6f8e 55%,#3b3446)"></div>
</section>

<section class="service light" style="height:376px">
  <div class="photo" role="img" aria-label="Photograph of an office partition with decorative film" style="background:linear-gradient(135deg,#e6ecf1,#b7c3cf 50%,#7e8c98)"></div>
  <div class="panel blue"><h2>Decorative Films/Covering</h2><p>Enhance your decor with our extensive range of Decorative Films and Coverings. Give a melamine desk a new hardwood finish or a glass cabinet a modern stone look. Make a wall into a textured feature or some glass into a decorative window. Whether it is in the kitchen or the bedroom, the office or the boardroom, our range of Decorative Films and Coverings meets every need. Our team of experienced installers can come on site so we can provide you with a finish to suit the other options that meet all customers' requirements. The design team can come up with artwork specific to clients' demands, or can incorporate your designs into existing environments. We can provide full art proofs so you can see what the application will look like before it is applied. Our innovative films are cutting edge, so look as good in a just-opened office complex as they do in a rejuvenated kitchen front. We have the right product for every interior decoration job.</p></div>
</section>

<section class="service dark" style="height:312px">
  <div class="panel dark"><h2>Kitchen Refurbishing/Rejuvenating</h2><p>Our kitchen building and design experience means that Lumen Interiors can meet all our customers' needs. We can create the best finish for any age kitchen, giving old kitchens life and making new kitchens feel homely. With our experience and product knowledge we have access to innovative and creative applications that make our Kitchen Refurbishing and Rejuvenating techniques perfect for both high level architects and DIY home renovators. We can create personalised and stylised looks for your kitchen, without having to start from scratch. Our range of finishes suits all panel types and existing surfaces, so there is an application for all the kitchen environments you are looking to enhance.</p></div>
  <div class="photo" role="img" aria-label="Photograph of a renovated grey kitchen" style="background:linear-gradient(135deg,#d9d9d7,#9a9a96 55%,#4e4e4c)"></div>
</section>

<section class="service light" style="height:326px">
  <div class="photo" role="img" aria-label="Photograph of a timber panelled feature wall with red chairs" style="background:linear-gradient(135deg,#c9a77c,#9b7550 50%,#6b4a31)"></div>
  <div class="panel blue"><h2>Feature Walls</h2><p>Make your feature wall something that jumps out and says hello or something that sits serenely in the background and makes you feel comfortable and at ease. Lumen Interiors has the Feature Wall solution that will work with any space you are trying to enhance. Whether it is a high definition photo quality image, a custom design or a texture fill, a Lumen Feature Wall will achieve the look and feel you want for your room. We provide a range of digital printing techniques that can meet varied needs, such as HD quality images, artistic patterns and designs, and a kaleidoscope of colours, all in an array of textures and finishes that make every Feature Wall look good. Take your room to the next level with our Custom Printed Feature Walls with Textured Laminates.</p></div>
</section>

<section class="service dark" style="height:304px">
  <div class="panel dark"><h2>Custom Printed Wallpaper</h2><p>At Lumen Interiors we have a custom wallpaper solution for every requirement. Whether you are trying to enhance the wall behind the computer in your office or an entire hotel, our Custom Printed Wallpaper meets all needs. We have a range of adhesive options both permanent and removable, which means the Lumen team can do the installation for you or we can provide options for self installation or for an experienced wallpaper installer. Our design team can create the right image for your Custom Wallpaper, you can bring your own designs or we can work together to collaborate on a design that works for the space you are looking to transform. Take your room to the next level with our Custom Printed Feature Walls with Textured Laminates.</p></div>
  <div class="photo" role="img" aria-label="Photograph of an office with a printed wallpaper mural" style="background:linear-gradient(135deg,#d6dde3,#8f9ba6 55%,#505b64)"></div>
</section>

<section class="service light" style="height:248px">
  <div class="photo" role="img" aria-label="Photograph of a blue patterned feature wall" style="background:linear-gradient(135deg,#a9c8e0,#5f90ba 50%,#2f5f88)"></div>
  <div class="panel blue"><h2>Custom Printed Feature Walls</h2><p>At Lumen Interiors we offer a unique range of finishes that can take your feature wall to another level. The superior range of textured finishes and custom print options we have available makes any room we enhance the decor in all the more impressive when we complete it with our specialist products. If you are looking to impress, whether it is in your office or in your home, our Custom Feature Walls are just what you are looking for.</p></div>
</section>

<section class="service dark" style="height:280px">
  <div class="panel dark"><h2>Kids rooms</h2><p>With the interior decoration applications we use at Lumen Interiors we can make any child's bedroom into the room of their dreams. We can create an environment that is one that they will remember forever, with the fairies, warriors, cartoon characters or sports heroes of their youth, all potential aspects of their room design. Our range of print and design options means we can bring to life any bedroom idea you or your child has. With Printed Feature Walls and Custom Designed Interiors we can make any kids room into one they will cherish for life.</p></div>
  <div class="photo" role="img" aria-label="Photograph of a colourful children's bedroom" style="background:linear-gradient(135deg,#9fd0cf,#4f9aa3 50%,#b3473e)"></div>
</section>

<section class="service light" style="height:376px">
  <div class="photo" role="img" aria-label="Photograph of frosted glass office windows" style="background:linear-gradient(135deg,#eef2f4,#c3ced6 50%,#8897a2)"></div>
  <div class="panel blue"><h2>Window Treatments</h2><p>Lumen Interiors window design range means that we have a finish for every glass or window treatment you require. Whether it is for privacy film, to keep people out, or decorative film, to bring people closer, we have a glass finish for every occasion. Many of our custom wallpapers work just as well on glass, so can be used as a complete wall-to-ceiling application or in pieces and patterns on glass to provide for all decorative requirements. For privacy we have complete block out options in multiple designs and colours, as well as frosted films or light diffusers that offer varying levels of opacity perfect for every situation. Our frosted glass film options both in the home and office environment, can come as a flat finish, to provide complete privacy or with cut patterns or designs to add a personalised touch to your interior environment. If you want to make your window a design element in the space you are working with, then a Lumen Interiors Window Treatment will give you exactly this.</p></div>
</section>

<section class="service dark" style="height:242px">
  <div class="panel dark"><h2>Wall Art</h2><p>Turn your wall into a work of art. Or make art come to life on your wall. At Lumen Interiors we can make any wall into something special and unique. We have access to a massive range of existing high quality artwork or we can do something more custom just for you. Our exclusive range of finishes and printing techniques means that we can achieve a Wall Art design for all types of interior decoration requirements. If you want to put your own design on your wall or you want us to come up with a design just for you, Lumen Interiors Wall Art options are going to meet your needs.</p></div>
  <div class="photo" role="img" aria-label="Photograph of a living room with large wall art" style="background:linear-gradient(135deg,#e9e4dc,#b9ad9c 55%,#6f665b)"></div>
</section>

<section class="cta">
  <span class="cta-text">Take a look at all what we offer you</span>
  <span class="cta-btn">Check it Out</span>
</section>

<footer class="footer">
  <div class="brand"><span class="brand-mark"></span><span class="brand-name">Lumen Interiors</span></div>
  <p class="footer-about">The Lumen Interiors team have over 20 years experience in the design, building, vinyl application and signage trades, giving us the ability to work through any interior or architectural needs your project may require.</p>
  <p class="footer-copy">© 2015, Lumen Interiors All rights reserved</p>
  <div class="col contact"><h3>Contact Us</h3><p>hello@lumeninteriors.example</p><p>02 5550 1840</p></div>
  <div class="col follow"><h3>Follow Us</h3><div class="socials"><span></span><span></span><span></span></div></div>
  <div class="payments"><span></span><span></span><span></span><span></span><span></span></div>
  <div class="to-top"><span>Top</span>
    <svg width="30" height="30" viewBox="0 0 30 30"><circle cx="15" cy="15" r="14" fill="none" stroke="#ffffff" stroke-width="1.5"/><path d="M9 18l6-6 6 6" fill="none" stroke="#ffffff" stroke-width="2"/></svg>
  </div>
</footer>
</body>
</html>
```